Tech Savy small Business accountant business card design

We need a business card for a new company based in the cloud. We provide tax, business advisory, accounting, information technology solutions and back office functions to small businesses. We offer fixed fee packages with add on services as you need them. By harnessing technology we simplify small business operational processes providing valuable time and information for small business owners to grow their business. In the logo (bluvoria) we want to be able to see bluv and experts. The final design should communicate achieving growth dreams and balance (ie life and $).
Updates
This project has been temporarily placed on hold until I finalize "Tech Savy small Business accountant needs a logo". I invite all designers to submit on this logo project. Once my logo is finalized I will resume this business card contest. Thanks Added Wednesday, March 19, 2014
This project has been temporarily placed on hold until I finalize "Tech Savy small Business accountant logo". I invite all designers to submit on this logo project. Once my logo is finalized I will resume this business card contest. Thanks Added Thursday, March 20, 2014
Target Market(s)
Small Business (Revenue $500,000, more than 3 employees) owners.
Industry/Entity Type
Small Business
Contact Information for Business Card
Marcy Elwind (Principal)
Accountant, Tax Agent.
TEL | 0417 683 912
EMAIL | Marcy.Elwind@bluvoria.com.au
WEB | www.bluvoria.com.au
Look and feel

```html
<!DOCTYPE html>
<html lang="en">
<head>
<meta charset="utf-8">
<title>bluvoria business card</title>
<link rel="stylesheet" href="https://fonts.googleapis.com/css2?family=Ubuntu:wght@400;500;700&display=swap">
<style>
  :root {
    --page: #ecebe8;
    --card-dark: #0b0c0e;
    --blue: #2a9be0;
    --blue-deep: #1a7cc4;
    --grey-text: #9a9ca0;
    --grey-logo: #7f8186;
    --white: #ffffff;
  }
  * { margin: 0; padding: 0; box-sizing: border-box; }
  html, body { width: 1200px; height: 913px; overflow: hidden; }
  body {
    background: var(--page);
    font-family: "Ubuntu", "Helvetica Neue", Arial, sans-serif;
    position: relative;
  }
  .card {
    position: absolute;
    width: 560px;
    height: 320px;
    border-radius: 18px;
    overflow: hidden;
    box-shadow: 0 10px 28px rgba(0,0,0,0.18);
  }
  .card-front { left: 70px; top: 110px; background: var(--card-dark); }
  .card-back { left: 570px; top: 480px; background: var(--white); }

  .edge-band {
    position: absolute;
    left: 0;
    top: 0;
    bottom: 0;
    width: 36px;
    background: linear-gradient(180deg, var(--blue), var(--blue-deep));
  }
  .edge-rule {
    position: absolute;
    left: 48px;
    top: 0;
    bottom: 0;
    width: 4px;
    background: var(--blue-deep);
    opacity: 0.6;
  }

  .front-content {
    position: absolute;
    right: 34px;
    top: 34px;
    text-align: right;
    color: var(--blue);
  }
  .wordmark {
    font-weight: 500;
    font-size: 46px;
    letter-spacing: -1px;
    line-height: 1;
    color: var(--grey-text);
  }
  .tagline {
    font-size: 14px;
    color: var(--grey-text);
    margin-top: 4px;
  }
  .person { margin-top: 26px; }
  .person-name {
    font-weight: 700;
    font-size: 21px;
    color: var(--blue);
    letter-spacing: 0.3px;
  }
  .person-role {
    font-size: 13px;
    color: var(--grey-text);
    margin-top: 3px;
  }
  .contact-list {
    list-style: none;
    margin-top: 22px;
    font-size: 13px;
    line-height: 21px;
    color: var(--blue);
  }
  .contact-list li { display: flex; justify-content: flex-end; align-items: center; gap: 8px; }
  .contact-icon { width: 12px; height: 12px; flex: none; }

  .back-content {
    position: absolute;
    right: 48px;
    top: 108px;
    text-align: left;
  }
  .back-content .wordmark { font-size: 60px; color: var(--grey-logo); }
  .back-content .tagline { font-size: 17px; color: var(--grey-logo); margin-top: 6px; }
</style>
</head>
<body>

<article class="card card-front" aria-label="Card front">
  <div class="edge-band" aria-hidden="true"></div>
  <div class="edge-rule" aria-hidden="true"></div>
  <div class="front-content">
    <div class="wordmark">bluvoria</div>
    <div class="tagline">Your business and accounting partner</div>
    <div class="person">
      <div class="person-name">MARCY ELWIND (Principal)</div>
      <div class="person-role">Accountant, Tax Agent</div>
    </div>
    <ul class="contact-list">
      <li>0417 683 912
        <svg class="contact-icon" viewBox="0 0 12 12" aria-hidden="true"><path d="M2.5 1 L4.5 1 L5.2 3.5 L4 4.5 Q5 7 7.5 8 L8.5 6.8 L11 7.5 L11 9.5 Q10 11 8 11 Q1 9 1 2.5 Q1.2 1.2 2.5 1 Z" fill="none" stroke="var(--grey-text)" stroke-width="1"/></svg>
      </li>
      <li>www.bluvoria.com.au
        <svg class="contact-icon" viewBox="0 0 12 12" aria-hidden="true"><g fill="none" stroke="var(--grey-text)" stroke-width="1"><circle cx="6" cy="6" r="5"/><ellipse cx="6" cy="6" rx="2.2" ry="5"/><line x1="1" y1="6" x2="11" y2="6"/></g></svg>
      </li>
      <li>Marcy.Elwind@bluvoria.com.au
        <svg class="contact-icon" viewBox="0 0 12 12" aria-hidden="true"><g fill="none" stroke="var(--grey-text)" stroke-width="1"><rect x="1" y="2.5" width="10" height="7"/><polyline points="1,2.5 6,7 11,2.5"/></g></svg>
      </li>
    </ul>
  </div>
</article>

<article class="card card-back" aria-label="Card back">
  <div class="back-content">
    <div class="wordmark">bluvoria</div>
    <div class="tagline">Your business and accounting partner</div>
  </div>
</article>

</body>
</html>
```